New Business Card Design Project LORVANTI-Italy

we are LORVANTI-Italy
our company in the market for 3 years we are luxury cosmetic company and its about time for a facelift :)
i will like to have elegant luxurious and unique business card
that will give the person that get it a unique, luxurious and elegant impression
I'm VERY OPEN FOR NEW IDEAS , even duo i add a few files of things that i see on line and i like them

i add my logo as well
my website is LORVANTI.COM
(if you would like to see the main style that we have)

Target Market(s)

adult that have money :)

Industry/Entity Type

Business

Contact Information for Business Card

Name - Dario Lorvanti
Position - CEO and CO Founder
address - 4817 E Halvern
telephone - 555-384-1926
email - dario@lorvanti.com
fax - 555-384-1926
website - LORVANTI.COM

Colors
000000
959595
fbee3e
ffffff

Requirements
Must have
• big logo in GOLD color
• elegant look
• impressive
Nice to have
• not must but maybe classy pattern background
• not must but maybe emblem
• maybe clear plastic business card
Should not have
• colors
• images

```html
<!DOCTYPE html>
<html lang="en">
<head>
<meta charset="utf-8">
<title>LORVANTI Italy – Business Card</title>
<link href="https://fonts.googleapis.com/css2?family=Cinzel:wght@400;700&family=Open+Sans:wght@400&display=swap" rel="stylesheet">
<style>
  :root {
    --backdrop: #d0d0d0;
    --gold: #c6a236;
    --gold-bright: #d8b440;
    --ink: #000000;
    --paper: #ffffff;
  }
  html, body {
    margin: 0;
    width: 1200px;
    height: 900px;
    overflow: hidden;
    background: var(--backdrop);
  }
  .canvas {
    position: relative;
    width: 1200px;
    height: 900px;
  }
  .card {
    position: absolute;
    top: 271px;
    width: 457px;
    height: 281px;
    border-radius: 14px;
    overflow: hidden;
    box-shadow: 2px 3px 5px rgba(0,0,0,0.25);
  }
  .card--front { left: 137px; background: var(--gold); }
  .card--back { left: 626px; background: var(--ink); }

  .front-panel { position: absolute; left: 0; top: 0; }

  .brand-mark {
    position: absolute;
    left: 32px;
    top: 68px;
    width: 146px;
    height: 146px;
    border: 3px solid var(--gold);
    border-radius: 50%;
    box-sizing: border-box;
    display: flex;
    align-items: center;
    justify-content: center;
  }
  .brand-mark__name {
    font-family: "Cinzel", serif;
    font-weight: 700;
    font-size: 19px;
    color: var(--gold);
    letter-spacing: 1px;
  }

  .contact {
    position: absolute;
    left: 247px;
    top: 58px;
    color: var(--paper);
    font-family: "Open Sans", sans-serif;
  }
  .contact__name {
    font-family: "Cinzel", serif;
    font-weight: 700;
    font-size: 19px;
    margin: 0;
    line-height: 1.2;
  }
  .contact__role {
    font-size: 12.5px;
    margin: 1px 0 17px;
  }
  .contact__list { list-style: none; margin: 0; padding: 0; }
  .contact__item {
    display: flex;
    align-items: center;
    gap: 6px;
    font-size: 12.5px;
    height: 21px;
  }
  .contact__icon { width: 15px; height: 15px; flex: none; }
  .contact__address { font-size: 12.5px; margin-top: 16px; }

  .back-brand {
    position: absolute;
    inset: 0;
    display: flex;
    flex-direction: column;
    align-items: center;
    color: var(--gold-bright);
    font-family: "Cinzel", serif;
    font-weight: 400;
  }
  .back-brand__circle {
    margin-top: 41px;
    width: 100px;
    height: 100px;
    border: 3px solid var(--gold-bright);
    border-radius: 50%;
    box-sizing: border-box;
  }
  .back-brand__name { font-size: 40px; margin-top: 14px; line-height: 1; letter-spacing: 1px; }
  .back-brand__region { font-size: 16px; margin-top: 14px; letter-spacing: 1px; }
</style>
</head>
<body>
<main class="canvas">

  <section class="card card--front">
    <svg class="front-panel" width="457" height="281" viewBox="0 0 457 281">
      <path d="M0 0 H91 A143 143 0 0 1 91 281 H0 Z" fill="var(--paper)"/>
    </svg>
    <div class="brand-mark"><span class="brand-mark__name">LORVANTI</span></div>

    <div class="contact">
      <h1 class="contact__name">DARIO LORVANTI</h1>
      <p class="contact__role">CEO and CO Founder</p>
      <ul class="contact__list">
        <li class="contact__item">
          <svg class="contact__icon" viewBox="0 0 16 16"><circle cx="8" cy="8" r="8" fill="#fff"/><path d="M4.5 6.5 Q8 3.5 11.5 6.5 L10.5 7.5 L9.5 6.8 H6.5 L5.5 7.5 Z M5.5 8.5 H10.5 V11 H5.5 Z" fill="var(--gold)"/></svg>
          555-384-1926
        </li>
        <li class="contact__item">
          <svg class="contact__icon" viewBox="0 0 16 16"><circle cx="8" cy="8" r="8" fill="#fff"/><rect x="5" y="4.5" width="6" height="3" fill="var(--gold)"/><rect x="4" y="7.5" width="8" height="4" rx="1" fill="var(--gold)"/></svg>
          555-384-1926
        </li>
        <li class="contact__item">
          <svg class="contact__icon" viewBox="0 0 16 16"><circle cx="8" cy="8" r="8" fill="#fff"/><rect x="4" y="5" width="8" height="6" fill="var(--gold)"/><path d="M4 5 L8 8.5 L12 5" stroke="#fff" stroke-width="1" fill="none"/></svg>
          dario@lorvanti.com
        </li>
        <li class="contact__item">
          <svg class="contact__icon" viewBox="0 0 16 16"><circle cx="8" cy="8" r="8" fill="#fff"/><circle cx="8" cy="8" r="4" fill="none" stroke="var(--gold)" stroke-width="1.4"/><path d="M4 8 H12 M8 4 V12" stroke="var(--gold)" stroke-width="1"/></svg>
          WWW.LORVANTI.COM
        </li>
      </ul>
      <p class="contact__address">4817 E Halvern</p>
    </div>
  </section>

  <section class="card card--back">
    <div class="back-brand">
      <div class="back-brand__circle"></div>
      <div class="back-brand__name">LORVANTI</div>
      <div class="back-brand__region">ITALY</div>
    </div>
  </section>

</main>
</body>
</html>
```